Retail Jewelry Business Card Design Project

We are in need of a new business card design for a retail jewelry store. This store is in the business of fine jewelry including but not specific to bridal jewelry, diamonds, designer jewelry and watches.

This store has been in business for 20 years but continues to strive for a modern professional appeal. The main colors use for this business are a royal blue, white and silver.

Target Market(s)

Target market is ages 18-50

Industry/Entity Type

Jewelry

Requirements
Must have
• Sales Person Name
Sales Person Email Address

Store Address
Store Phone
Website

Standard business card size. No odd shapes or sizes.
Nice to have
• Overall modern feel for card.

We have thought that a design with a nice feature of the logo on the back of the card would be nice but open to ideas.
Should not have
• No specific images of jewelry should be used.

```html
<!DOCTYPE html>
<html lang="en">
<head>
<meta charset="utf-8">
<title>Marlowe Grant Fine Jewelry – Business Card</title>
<link rel="stylesheet" href="https://fonts.googleapis.com/css2?family=Jost:wght@400;500;600&display=swap">
<style>
  :root {
    --royal-blue: #2d2c8e;
    --text-dark: #3a3a44;
    --divider: #b9b9c4;
    --card-white: #ffffff;
    --backdrop: #ecebef;
    --card-shadow: rgba(30, 30, 60, 0.14);
  }
  * { box-sizing: border-box; margin: 0; padding: 0; }
  html, body {
    width: 1200px;
    height: 750px;
    overflow: hidden;
    background: var(--backdrop);
    font-family: "Jost", Arial, sans-serif;
  }
  .canvas {
    width: 1200px;
    height: 750px;
    display: flex;
    align-items: center;
    justify-content: center;
    gap: 60px;
  }
  .card {
    position: relative;
    width: 525px;
    height: 300px;
    background: var(--card-white);
    box-shadow: 0 6px 22px var(--card-shadow);
  }
  .brand {
    position: absolute;
    left: 0;
    right: 0;
    text-align: center;
    color: var(--royal-blue);
    font-weight: 500;
    line-height: 1.15;
    letter-spacing: 0.02em;
  }
  .brand__name { display: block; font-size: 46px; }
  .brand__tagline { display: block; font-size: 22px; letter-spacing: 0.2em; text-transform: uppercase; }

  /* front */
  .card--front .brand { top: 38px; }
  .contact {
    position: absolute;
    left: 0;
    right: 0;
    bottom: 44px;
    display: flex;
    justify-content: center;
    align-items: flex-end;
  }
  .contact__person {
    text-align: right;
    padding-right: 16px;
    border-right: 1px solid var(--divider);
  }
  .contact__name {
    color: var(--royal-blue);
    font-weight: 600;
    font-size: 19px;
    margin-bottom: 6px;
  }
  .contact__address {
    color: var(--text-dark);
    font-size: 14px;
    line-height: 1.35;
  }
  .contact__channels {
    list-style: none;
    padding-left: 14px;
    color: var(--text-dark);
    font-size: 14px;
    line-height: 1.75;
  }
  .contact__channels li { display: flex; align-items: center; gap: 7px; }
  .icon { width: 12px; height: 12px; flex: none; }

  /* back */
  .card--back .brand { top: 80px; }
  .card--back .website {
    position: absolute;
    left: 0;
    right: 0;
    top: 204px;
    text-align: center;
    color: var(--royal-blue);
    font-size: 14px;
    letter-spacing: 0.24em;
  }
</style>
</head>
<body>
<main class="canvas">

  <section class="card card--front" aria-label="Business card front">
    <h1 class="brand">
      <span class="brand__name">Marlowe Grant</span>
      <span class="brand__tagline">Fine Jewelry</span>
    </h1>
    <div class="contact">
      <div class="contact__person">
        <p class="contact__name">Marlowe Grant Ellison</p>
        <p class="contact__address">2210 Bayview Street<br>Port Allen, FL 32450</p>
      </div>
      <ul class="contact__channels">
        <li>
          <svg class="icon" viewBox="0 0 12 12" aria-hidden="true"><circle cx="6" cy="6" r="5.3" fill="none" stroke="#3a3a44" stroke-width="1"/><path d="M4 3.2 L5.2 3.2 L5.6 4.8 L4.9 5.3 Q5.6 6.8 6.9 7.3 L7.4 6.6 L8.9 7 L8.9 8.2 Q6 8.6 4.1 6 Q3.4 4.6 4 3.2 Z" fill="#3a3a44"/></svg>
          555-014-2290
        </li>
        <li>
          <svg class="icon" viewBox="0 0 12 12" aria-hidden="true"><circle cx="6" cy="6" r="6" fill="#3a3a44"/><rect x="2.8" y="3.9" width="6.4" height="4.4" fill="#fff"/><path d="M2.8 3.9 L6 6.4 L9.2 3.9" fill="none" stroke="#3a3a44" stroke-width="0.7"/></svg>
          marlowe@marlowegrantjewelry.com
        </li>
        <li>
          <svg class="icon" viewBox="0 0 12 12" aria-hidden="true"><circle cx="6" cy="6" r="5.5" fill="#3a3a44"/><ellipse cx="6" cy="6" rx="2.3" ry="5.3" fill="none" stroke="#fff" stroke-width="0.7"/><path d="M0.8 6 H11.2 M1.6 3.6 H10.4 M1.6 8.4 H10.4" stroke="#fff" stroke-width="0.6"/></svg>
          www.marlowegrantjewelry.com
        </li>
      </ul>
    </div>
  </section>

  <section class="card card--back" aria-label="Business card back">
    <h2 class="brand">
      <span class="brand__name">Marlowe Grant</span>
      <span class="brand__tagline">Fine Jewelry</span>
    </h2>
    <p class="website">www.marlowegrantjewelry.com</p>
  </section>

</main>
</body>
</html>
```